Online tuition webpage design needed

Hi,
We are starting up an online tuition website for non- English speakers wishing to take an TOVAR test.

The webpage must include a place for people to enroll online in the course.
The home page must have:
• room for a logo (coming shortly, blue in colour)
• different packages of online tuition and paywick
• tool bar showing different pages
• perhaps a video, small pictures

This is my site currently:-

www.lexavotutoring.com

as you can see, I am not very sure how to create a website … The large logo is what I would like to use, but I project has not been finalized yet. Please note, I don’t like the logo being that large!

Sites that are similar to what I am doing and like the design of are:

http://www.brindacourse.com.au/fees

https://www.quorvel9x.net/index.php

http://www.lessonmasterpercival.co.uk/index.html

http://www.tamrunexamhub.com/

One thing I need is a place for student s to enroll, and if possible, I would like to use learnix to create exercises for students.
Currently, my site is using sitecraft. My preference is to use learnix for online activities. I am not sure if I can use both.
Thanks in advance

Target Market(s)

people wising to take an TOVAR test (English proficiency test)

Industry/Entity Type

Online

Colors
3276b5
0292cd

Requirements
Must have
• a place for enrollment and admin login for students
learnix
video
voxly, friendbook, chirpnet logos
Nice to have
• a booking calender
Should not have
• too much clutter. must be clean and professional looking

```html
<!DOCTYPE html>
<html lang="en">
<head>
<meta charset="utf-8">
<title>TOVAR Online Tuition</title>
<link href="https://fonts.googleapis.com/css2?family=Open+Sans:wght@400;600;700&display=swap" rel="stylesheet">
<style>
:root{
  --stage:#3276b5;
  --brand:#0292cd;
  --brand-deep:#0a68b6;
  --nav-active:#0a6db0;
  --ink:#333;
  --muted:#6b6b6b;
  --link:#1a86c8;
  --footer:#333333;
  --footer-ink:#e8e8e8;
  --white:#fff;
}
*{margin:0;padding:0;box-sizing:border-box}
html,body{width:746px;height:1200px;overflow:hidden}
body{background:var(--stage);font-family:"Open Sans",sans-serif;color:var(--ink);position:relative}
.page{position:absolute;left:106px;top:26px;width:534px;height:1150px;background:var(--white)}
.abs{position:absolute}
/* header */
.logo{left:14px;top:10px;display:flex;align-items:center;gap:6px}
.logo-dot{width:40px;height:40px;border-radius:50%;background:var(--brand-deep)}
.logo-name{font-size:30px;font-weight:600;color:var(--brand-deep);line-height:1}
.logo-sub{left:73px;top:50px;font-size:12px;color:#3a4a7a}
.login-title{left:297px;top:24px;font-size:7px;font-weight:700;color:var(--brand)}
.remember{left:389px;top:24px;font-size:5px;color:var(--brand)}
.field{height:14px;border:1px solid #cfd8de;font-size:5px;color:#aaa;padding:3px 3px}
.btn{background:var(--brand);color:var(--white);font-size:7px;font-weight:700;text-align:center;line-height:14px;width:40px;height:14px}
/* nav */
.nav{left:0;top:76px;width:534px;height:27px;background:var(--brand);display:flex;z-index:2}
.nav a{color:var(--white);font-size:7.5px;font-weight:600;text-decoration:none;line-height:27px;text-align:center;border-right:1px solid rgba(255,255,255,.15)}
.nav a.active{background:var(--nav-active)}
/* hero */
.hero{left:0;top:103px;width:534px;height:234px;background:linear-gradient(135deg,#8a6b57 0%,#d9c3b0 35%,#f0e7de 55%,#b88f72 80%,#6f5446 100%)}
.hero-badge{left:317px;top:136px;width:164px;height:164px;border-radius:50%;background:rgba(255,255,255,.78);text-align:center;padding-top:37px}
.hero-badge .kicker{font-size:7px;font-weight:700;color:#333}
.hero-badge h1{font-size:9.5px;font-weight:700;color:var(--brand);margin-bottom:18px}
.hero-badge p{font-size:6.3px;color:#444;line-height:9.5px;padding:0 12px;margin-bottom:6px}
.arrows{font-size:12px;color:var(--brand-deep)}
/* packages */
.pack{top:363px;width:162px;height:277px;background:var(--brand);color:var(--white);padding:15px 15px 0 15px}
.pack.featured{background:var(--brand-deep);box-shadow:0 0 6px rgba(0,0,0,.35)}
.pack h2{font-size:16px;font-weight:700;letter-spacing:.5px;height:40px}
.pack .desc{font-size:7.5px;line-height:9px;height:62px}
.pack ul{list-style:none;font-size:7.5px;line-height:13.3px}
.pack li{padding-left:11px;position:relative}
.pack li.tick::before{content:"✔";position:absolute;left:0;font-size:6px}
.price{text-align:center;font-size:29px;font-weight:700;margin-top:9px;line-height:34px}
.price small{font-size:18px}
.enroll{text-align:center;font-size:11px;font-weight:700;margin-top:5px}
.pack-icon{right:10px;top:14px;width:18px;height:22px}
.paywick{left:460px;top:643px;width:61px;text-align:right;font-size:10px;font-weight:700;color:#253b80}
/* intro */
.intro-title{left:12px;top:665px;font-size:16px;font-weight:700;color:var(--link)}
.intro-text{left:12px;top:697px;width:330px;font-size:6.8px;line-height:9.5px;color:var(--link)}
.intro-list{left:22px;top:723px;list-style:none;font-size:6.8px;line-height:15px;color:var(--link)}
.intro-list li::before{content:"◤";font-size:4px;margin-right:6px;color:#666}
/* calendar */
.calendar{left:370px;top:669px;width:151px;height:123px;border:1px solid #9cc9e6}
.cal-head{background:var(--brand);color:var(--white);font-size:7px;font-weight:700;padding:3px 10px;height:15px}
.calendar table{margin:6px auto 0;border-collapse:collapse;font-size:7px}
.calendar th{font-weight:400;color:var(--brand-deep);width:19px;height:15px}
.calendar td{text-align:center;height:10.5px;color:#333}
.cal-nav{left:12px;bottom:6px;width:126px;display:flex;justify-content:space-between;font-size:7px;font-weight:700;color:var(--brand-deep)}
/* video */
.video-title{left:13px;top:811px;font-size:14px;font-weight:700;color:var(--link)}
.video{left:134px;top:836px;width:267px;height:152px;background:linear-gradient(180deg,#3f4a34 0%,#2c3626 50%,#1c2218 100%)}
.play{left:111px;top:47px;width:45px;height:45px}
.controls{left:9px;top:128px;width:250px;height:14px}
/* footer */
.footer{left:0;top:1016px;width:534px;height:134px;background:var(--footer);color:var(--footer-ink)}
.foot-h{font-size:9.5px;font-weight:700;color:var(--brand);top:20px}
.foot-list{left:12px;top:35px;list-style:none;font-size:7.5px;line-height:13.3px}
.foot-list li::before{content:"◤";font-size:4px;margin-right:6px}
.social{display:flex;align-items:center;gap:5px;font-size:9.5px;font-weight:700;height:19px}
.social .dot{width:14px;height:14px;border-radius:50%;background:#4a6fa5}
.social .ring{width:15px;height:15px;border-radius:50%;border:2px solid var(--brand)}
.posts{left:384px;top:36px;width:140px;font-size:6.5px;line-height:10.5px}
.foot-nav{left:12px;top:113px;display:flex;font-size:6.8px;font-weight:600}
.foot-nav span{margin-right:26px}
.copy{left:12px;top:129px;font-size:6px;color:#6a6a6a}
</style>
</head>
<body>
<main class="page">
  <header>
    <div class="abs logo"><span class="logo-dot"></span><span class="logo-name">TOVAR</span></div>
    <div class="abs logo-sub">Online Tuition</div>
    <div class="abs login-title">STUDENTS LOGIN</div>
    <div class="abs remember">☑ Remember Password?</div>
    <div class="abs field" style="left:298px;top:34px;width:88px">User Name</div>
    <div class="abs field" style="left:389px;top:34px;width:88px">Password</div>
    <div class="abs btn" style="left:482px;top:34px">LOGIN</div>
    <div class="abs field" style="left:298px;top:54px;width:179px;text-align:right;color:#9ab">&#9906;</div>
    <div class="abs btn" style="left:482px;top:54px">SEARCH</div>
  </header>

  <nav class="abs nav">
    <a class="active" style="margin-left:14px;width:48px">HOME</a>
    <a style="width:106px">TUTORIAL PACKAGES</a>
    <a style="width:96px">TIPS &amp; COMMENTS</a>
    <a style="width:64px">READING</a>
    <a style="width:62px">SPEAKING</a>
    <a style="width:74px">LISTERNING</a>
    <a style="width:70px;border:none">WRITING</a>
  </nav>

  <section class="abs hero" role="img" aria-label="Photo of smiling students giving thumbs up"></section>
  <div class="abs hero-badge">
    <div class="kicker">WELCOME TO</div>
    <h1>TOVAR ONLINE TUITION</h1>
    <p>We put you first. We listen to you and help you find what you need.</p>
    <p>If you want help in passing an TOVAR test, we can help you Lessons in reading, writing, listening and speakingtips.</p>
    <div class="arrows">‹ ›</div>
  </div>

  <article class="abs pack" style="left:12px">
    <h2>SILVER</h2>
    <p class="desc">Last minute TOVAR preparation. Ideal for thosewho need to get familiar with test format and strategies.</p>
    <ul><li class="tick">90 days access</li><li class="tick">100 hours study time</li><li class="tick">Over 1000 Study Pages</li><li class="tick">Over 260 Interactive Activitie</li><li>Voice recording tools</li><li>Practice tests in all 4 modules</li></ul>
    <div class="price"><small>$</small>59</div>
    <div class="enroll">ENROLL NOW</div>
    <svg class="abs pack-icon" viewBox="0 0 18 22"><path d="M15 2 L4 17 L3 21 L6 18 L17 4Z" fill="#c94a5a"/></svg>
  </article>
  <article class="abs pack featured" style="left:187px">
    <h2>GOLD</h2>
    <p class="desc">Comprehensive TOVAR preparation. Ideal for those who want to improve their English skills and get familiar with the test format and strategies.</p>
    <ul><li class="tick">90 days access</li><li class="tick">100 hours study time</li><li class="tick">Over 1000 Study Pages</li><li class="tick">Over 260 Interactive Activitie</li><li class="tick">Voice recording tools</li><li>Practice tests in all 4 modules</li></ul>
    <div class="price"><small>$</small>79</div>
    <div class="enroll">ENROLL NOW</div>
    <svg class="abs pack-icon" viewBox="0 0 18 22"><circle cx="9" cy="7" r="4" fill="#8fb3d6"/><path d="M2 20 Q9 8 16 20Z" fill="#5d86b3"/></svg>
  </article>
  <article class="abs pack" style="left:360px">
    <h2>DIAMOND</h2>
    <p class="desc">Complete TOVAR preparation. Ideal for those who want to improve their English skills, get familiar with the test and receive personalised assessment</p>
    <ul><li class="tick">90 days access</li><li class="tick">100 hours study time</li><li class="tick">Over 1000 Study Pages</li><li class="tick">Over 260 Interactive Activitie</li><li class="tick">Voice recording tools</li><li class="tick">Practice tests in all 4 modules</li></ul>
    <div class="price"><small>$</small>99</div>
    <div class="enroll">ENROLL NOW</div>
    <svg class="abs pack-icon" viewBox="0 0 18 22"><path d="M15 2 L4 17 L3 21 L6 18 L17 4Z" fill="#c94a5a"/></svg>
  </article>
  <div class="abs paywick">Paywick</div>

  <h2 class="abs intro-title">TOVAR Online Tuition</h2>
  <p class="abs intro-text">We put you first. We listen to you and help you find what you need. If you want help in passing an TOVAR test, we can help you with the following criteria,</p>
  <ul class="abs intro-list">
    <li>Lessons in reading, writing, listening and speaking</li>
    <li>Professional teacher feedback and tips.</li>
    <li>Voxly and practice with native speakers.</li>
    <li>Quick Turnaround.</li>
    <li>Friendly and Approachable teachers</li>
  </ul>

  <aside class="abs calendar">
    <div class="cal-head">JANUARY 2014</div>
    <table>
      <tr><th>M</th><th>T</th><th>W</th><th>T</th><th>F</th><th>S</th><th>S</th></tr>
      <tr><td></td><td></td><td>1</td><td>2</td><td>3</td><td>4</td><td>5</td></tr>
      <tr><td>6</td><td>7</td><td>8</td><td>9</td><td>10</td><td>11</td><td>12</td></tr>
      <tr><td>13</td><td>14</td><td>15</td><td>16</td><td>17</td><td>18</td><td>19</td></tr>
      <tr><td>20</td><td>21</td><td>22</td><td>23</td><td>24</td><td>25</td><td>26</td></tr>
      <tr><td>27</td><td>28</td><td>29</td><td>30</td><td>31</td><td></td><td></td></tr>
    </table>
    <div class="abs cal-nav"><span>« DEC</span><span>DEC »</span></div>
  </aside>

  <h2 class="abs video-title">Video Tutorial</h2>
  <div class="abs video" role="img" aria-label="Video still of a forest">
    <svg class="abs play" viewBox="0 0 45 45"><circle cx="22.5" cy="22.5" r="20" fill="rgba(255,255,255,.15)" stroke="#ddd" stroke-width="2"/><path d="M17 13 L32 22.5 L17 32Z" fill="#ddd"/></svg>
    <svg class="abs controls" viewBox="0 0 250 14"><rect width="250" height="14" fill="rgba(0,0,0,.55)"/><path d="M5 4 L10 7 L5 10Z" fill="#fff"/><rect x="17" y="6" width="163" height="2" fill="#888"/><rect x="17" y="6" width="18" height="2" fill="#2a9fe0"/><circle cx="36" cy="7" r="2.5" fill="#ddd"/><text x="186" y="9.5" font-size="6" fill="#fff" font-family="Open Sans,sans-serif">1:03 / 4:59</text><path d="M222 5 h2 l3-2 v8 l-3-2 h-2Z" fill="#fff"/><path d="M236 3 h3 M236 3 v3 M246 3 h-3 M246 3 v3 M236 11 h3 M236 11 v-3 M246 11 h-3 M246 11 v-3" stroke="#fff" stroke-width="1.2"/></svg>
  </div>

  <footer class="abs footer">
    <div class="abs foot-h" style="left:12px">TOVAR ONLINE TUITION</div>
    <ul class="abs foot-list"><li>Reading</li><li>Speaking</li><li>Listening</li><li>Writing</li></ul>
    <div class="abs" style="left:147px;top:38px">
      <div class="social"><span class="dot"></span>Follow Us</div>
      <div class="social"><span class="dot" style="background:#3b8ed0"></span>Tweet Us</div>
      <div class="social"><span class="dot" style="background:#2f78b5"></span>Link with Us</div>
    </div>
    <div class="abs social" style="left:256px;top:38px"><span class="ring"></span>Voxly Call Id</div>
    <div class="abs foot-h" style="left:384px">LATEST POSTS</div>
    <p class="abs posts">Welcome To International English Tuition We put our customers first. We listen to you and help you find what you need. If you want help...</p>
    <div class="abs foot-nav"><span>Home</span><span>Tutorial Packages</span><span>Tips &amp; Comments</span><span>Reading</span><span>Speaking</span><span>Listerning</span><span>Writing</span></div>
    <div class="abs" style="left:505px;top:113px;font-size:6.8px;font-weight:600">Z4</div>
    <div class="abs copy">Copyright @ TOVAR Online Tuition. All Rights Reserved</div>
  </footer>
</main>
</body>
</html>
```